Business Card for Coastal Tundrabridge Advisory

We need a business card for Coastal Tundrabridge Advisory. The company website address is provided below. The company logo is attached. We provide specialized permafrost services to the mining, transportation, and oil & gas industries. The card should be prepared for:
Matthias Korhonen, PhD.
Coastal Tundrabridge Advisory
PO Box 418259
Quillwater, Alaska 99642
Direct: +1-907-555-0143
Email: mkorhonen@tundrabridgeadvisory.example
Website: www.coastaltundrabridgeadvisory.example

```html
<!DOCTYPE html>
<html lang="en">
<head>
<meta charset="utf-8">
<title>Coastal Tundrabridge Advisory – Business Card</title>
<link href="https://fonts.googleapis.com/css2?family=Roboto:wght@300;400;500;700&display=swap" rel="stylesheet">
<style>
  :root {
    --backdrop: #232323;
    --card: #111722;
    --ink: #ffffff;
    --ink-soft: #d9dce2;
    --rule: #8a8f99;
  }
  * { box-sizing: border-box; margin: 0; padding: 0; }
  html, body {
    width: 1200px; height: 711px; overflow: hidden;
    background: var(--backdrop);
    font-family: "Roboto", Arial, sans-serif;
    color: var(--ink);
  }
  .stage {
    width: 1200px; height: 711px;
    display: flex; align-items: center; justify-content: center; gap: 44px;
  }
  .card {
    width: 540px; height: 309px;
    background: var(--card);
    border-radius: 3px;
    position: relative;
    overflow: hidden;
    box-shadow: 0 10px 28px rgba(0,0,0,0.55);
  }
  /* Front */
  .card-front {
    display: flex; flex-direction: column; align-items: center; justify-content: center;
    text-align: center; padding: 0 34px;
  }
  .brand-name {
    font-weight: 700;
    text-transform: uppercase;
    letter-spacing: 3px;
    color: var(--ink);
    line-height: 1.15;
  }
  .card-front .brand-name { font-size: 30px; margin-top: -20px; }
  .services { position: absolute; left: 28px; right: 28px; bottom: 30px; }
  .services-title { font-size: 11px; font-weight: 700; letter-spacing: 0.3px; margin-bottom: 4px; }
  .services-text { font-size: 10.5px; font-weight: 400; color: var(--ink-soft); }
  /* Back */
  .card-back { display: flex; align-items: center; }
  .back-brand {
    width: 46%; padding-left: 32px; padding-right: 12px;
  }
  .back-brand .brand-name { font-size: 19px; letter-spacing: 2px; }
  .divider {
    position: absolute; left: 47%; top: 54px; bottom: 54px;
    width: 1px; background: var(--rule);
  }
  .contact { position: absolute; left: 51%; top: 62px; right: 18px; }
  .person-name { font-size: 23px; line-height: 1.1; font-weight: 400; }
  .person-name .given { font-weight: 700; }
  .person-name .family { font-weight: 300; }
  .person-title { font-size: 13px; font-weight: 700; margin: 3px 0 0 10px; }
  .address { font-size: 10.5px; font-weight: 400; color: var(--ink-soft); margin: 10px 0 0 14px; line-height: 1.45; }
  .contact-list { list-style: none; margin: 18px 0 0 14px; font-size: 9.5px; color: var(--ink-soft); }
  .contact-list li { display: flex; align-items: center; gap: 6px; line-height: 1.8; white-space: nowrap; }
  .contact-list svg { width: 10px; height: 10px; flex: none; }
</style>
</head>
<body>
<main class="stage">
  <section class="card card-front">
    <div class="brand-name">Coastal Tundrabridge Advisory</div>
    <div class="services">
      <p class="services-title">OUR SERVICES</p>
      <p class="services-text">We provide specialized permafrost services to the mining, transportation, and oil &amp; gas industries</p>
    </div>
  </section>

  <section class="card card-back">
    <div class="back-brand">
      <div class="brand-name">Coastal Tundrabridge Advisory</div>
    </div>
    <span class="divider" aria-hidden="true"></span>
    <div class="contact">
      <h1 class="person-name"><span class="given">Matthias</span> <span class="family">Korhonen</span></h1>
      <p class="person-title">PhD</p>
      <p class="address">PO Box 418259<br>Quillwater, Alaska 99642</p>
      <ul class="contact-list">
        <li>
          <svg viewBox="0 0 10 10" aria-hidden="true"><path d="M2 1 L3.6 1 L4.3 3 L3.2 3.8 Q4 5.8 6.2 6.8 L7 5.7 L9 6.4 L9 8 Q8.6 9 7.5 9 Q1 8.2 1 2.5 Q1 1 2 1 Z" fill="#fff"/></svg>
          +1-907-555-0143
        </li>
        <li>
          <svg viewBox="0 0 10 10" aria-hidden="true"><rect x="0.6" y="2" width="8.8" height="6.4" rx="0.6" fill="none" stroke="#fff" stroke-width="1"/><path d="M0.8 2.3 L5 5.6 L9.2 2.3" fill="none" stroke="#fff" stroke-width="1"/></svg>
          mkorhonen@tundrabridgeadvisory.example
        </li>
        <li>
          <svg viewBox="0 0 10 10" aria-hidden="true"><circle cx="5" cy="5" r="4.3" fill="none" stroke="#fff" stroke-width="1"/><ellipse cx="5" cy="5" rx="1.8" ry="4.3" fill="none" stroke="#fff" stroke-width="0.8"/><path d="M0.8 5 H9.2" stroke="#fff" stroke-width="0.8"/></svg>
          www.coastaltundrabridgeadvisory.example
        </li>
      </ul>
    </div>
  </section>
</main>
</body>
</html>
```